BOLD & MINIMALIST DESIGN NEEDED

We want a very bold but minimalistic business card design that is impactful and utilizes both sides of the business card. Our current logo is included for your use.

We want bold fonts and good use of negative space. We don't want the logo to overpower the design.

Target Market(s)

Professionals who are building new commercial buildings.

Industry/Entity Type

Construction

Contact Information for Business Card

Name, Title, email, office phone, cell phone, website

Font styles to use
Serif
Sans Serif

Requirements
Must have
• Bold design!

```html
<!DOCTYPE html>
<html lang="en">
<head>
<meta charset="utf-8">
<title>Ridgeway Design + Build – Business Card</title>
<link href="https://fonts.googleapis.com/css2?family=Montserrat:wght@400;500;800&display=swap" rel="stylesheet">
<style>
  :root {
    --bg: #b9b9b9;
    --card-white: #ffffff;
    --card-black: #1f1f1f;
    --ink: #2b2b2b;
    --green: #7cc242;
    --green-soft: #cfe8b6;
    --rule: #d9e9c9;
  }
  * { margin: 0; padding: 0; box-sizing: border-box; }
  html, body { width: 1200px; height: 802px; overflow: hidden; }
  body {
    background: var(--bg);
    font-family: "Montserrat", Arial, sans-serif;
    display: flex;
    align-items: center;
    justify-content: center;
    gap: 40px;
  }
  .card {
    position: relative;
    width: 540px;
    height: 309px;
    border-radius: 22px;
    overflow: hidden;
  }
  .card--front { background: var(--card-white); color: var(--ink); }
  .card--back { background: var(--card-black); display: flex; align-items: center; justify-content: center; }

  .front-curve { position: absolute; inset: 0; width: 100%; height: 100%; }

  .brand {
    display: flex;
    align-items: center;
    gap: 10px;
    font-weight: 800;
    text-transform: uppercase;
    line-height: 1.05;
  }
  .brand__mark { width: 14px; height: 14px; background: var(--green); flex: none; }
  .brand__name { font-size: 26px; letter-spacing: 0.5px; }
  .brand__name small { display: block; font-size: 13px; letter-spacing: 4px; }

  .card--front .brand { position: absolute; left: 36px; top: 120px; color: var(--ink); }
  .card--back .brand { color: #ffffff; }
  .card--back .brand__name { font-size: 40px; }
  .card--back .brand__name small { font-size: 18px; letter-spacing: 7px; margin-top: 4px; }
  .card--back .brand__mark { width: 20px; height: 20px; }

  .divider {
    position: absolute;
    left: 248px; top: 70px;
    width: 1px; height: 150px;
    background: var(--rule);
  }
  .contact { position: absolute; left: 272px; top: 58px; }
  .contact__name {
    color: var(--green);
    font-weight: 800;
    font-size: 21px;
    letter-spacing: 0.5px;
    text-transform: uppercase;
  }
  .contact__title { font-size: 12px; font-weight: 500; margin-bottom: 18px; }
  .contact__list { list-style: none; font-size: 12.5px; }
  .contact__list li { display: flex; align-items: center; gap: 8px; margin-bottom: 7px; }
  .contact__list svg { width: 11px; height: 11px; fill: var(--green); flex: none; }
  .contact__web strong { color: var(--green); font-weight: 500; }
</style>
</head>
<body>
  <section class="card card--front" aria-label="Card front">
    <svg class="front-curve" viewBox="0 0 540 309" preserveAspectRatio="none" aria-hidden="true">
      <path d="M540 150 C440 250 330 295 200 309 L540 309 Z" fill="var(--green-soft)"/>
      <path d="M540 162 C445 256 340 300 215 309 L540 309 Z" fill="var(--green)"/>
      <path d="M540 170 C450 262 350 304 235 309 L540 309 Z" fill="var(--card-white)"/>
    </svg>

    <div class="brand">
      <span class="brand__mark"></span>
      <span class="brand__name">Ridgeway<small>Design + Build</small></span>
    </div>

    <div class="divider"></div>

    <div class="contact">
      <p class="contact__name">Dorian Vale</p>
      <p class="contact__title">Owner/CEO</p>
      <ul class="contact__list">
        <li><svg viewBox="0 0 24 24"><path d="M6.6 10.8a15 15 0 0 0 6.6 6.6l2.2-2.2c.3-.3.7-.4 1-.2 1.1.4 2.3.6 3.6.6.6 0 1 .4 1 1V20c0 .6-.4 1-1 1A17 17 0 0 1 3 4c0-.6.4-1 1-1h3.5c.6 0 1 .4 1 1 0 1.3.2 2.5.6 3.6.1.3 0 .7-.2 1z"/></svg>07 5550 1200</li>
        <li><svg viewBox="0 0 24 24"><path d="M7 2h10a2 2 0 0 1 2 2v16a2 2 0 0 1-2 2H7a2 2 0 0 1-2-2V4a2 2 0 0 1 2-2zm0 3v13h10V5z"/></svg>0400 555 019</li>
        <li><svg viewBox="0 0 24 24"><path d="M2 5h20v14H2zm2 2v.5l8 5 8-5V7z"/></svg>info@ridgewaybuild.com</li>
        <li class="contact__web"><svg viewBox="0 0 24 24"><path d="M12 2a10 10 0 1 0 0 20 10 10 0 0 0 0-20zm0 2c1 1.3 1.8 3 2.1 5H9.9C10.2 7 11 5.3 12 4zM4.3 11h3.6c.1 1.6.4 3.1 1 4.4A8 8 0 0 1 4.3 11zm5.6 0h4.2c-.1 2-.9 3.8-2.1 5.5-1.2-1.7-2-3.5-2.1-5.5zm6.2 0h3.6a8 8 0 0 1-4.6 4.4c.6-1.3.9-2.8 1-4.4z"/></svg>www.<strong>ridgewaybuild</strong>.com</li>
      </ul>
    </div>
  </section>

  <section class="card card--back" aria-label="Card back">
    <div class="brand">
      <span class="brand__mark"></span>
      <span class="brand__name">Ridgeway<small>Design + Build</small></span>
    </div>
  </section>
</body>
</html>
```